Moravel Aesthetic Doctor

I require an elegant, luxurious looking business card for my aesthetic business. I am a doctor and that will set me aside from competitors. I am planning to provide home and spa based treatments to clients with high expectations. I have attached my logo.

```html
<!DOCTYPE html>
<html lang="en">
<head>
<meta charset="utf-8">
<title>Moravel Aesthetic Doctor – Business Card</title>
<link rel="stylesheet" href="https://fonts.googleapis.com/css2?family=Work+Sans:wght@400;500;600&display=swap">
<style>
  :root {
    --stage: #161616;
    --card: #262626;
    --card-edge: #1f1f1f;
    --accent: #12a9e8;
    --text: #ececec;
    --muted: #cfcfcf;
  }
  * { margin: 0; padding: 0; box-sizing: border-box; }
  html, body {
    width: 1200px; height: 900px; overflow: hidden;
    background: var(--stage);
    font-family: "Work Sans", Arial, sans-serif;
    color: var(--text);
  }
  .stage {
    width: 1200px; height: 900px;
    display: flex; flex-direction: column; align-items: center; justify-content: center;
    gap: 24px;
  }
  .card {
    position: relative;
    width: 700px; height: 400px;
    background: linear-gradient(135deg, var(--card-edge), var(--card) 55%, #2d2d2d);
    border-bottom: 6px solid var(--accent);
    overflow: hidden;
  }
  .brand {
    display: flex; align-items: center; gap: 16px;
  }
  .brand-dot {
    width: 64px; height: 64px; border-radius: 50%;
    border: 2px solid #bdbdbd;
    flex-shrink: 0;
  }
  .brand-name {
    color: var(--accent);
    font-weight: 500;
    line-height: 1.05;
    letter-spacing: 0.06em;
  }
  .brand-name .line-main { display: block; font-size: 48px; }
  .brand-name .line-sub { display: block; font-size: 20px; letter-spacing: 0.12em; }

  /* Front */
  .card-front .brand {
    position: absolute; top: 120px; left: 50%; transform: translateX(-50%);
  }
  .services {
    position: absolute; top: 262px; left: 0; right: 0;
    text-align: center; font-size: 17px; letter-spacing: 0.06em; line-height: 1.65;
    color: var(--text);
  }
  .services .sep { color: var(--accent); margin: 0 6px; }

  /* Back */
  .card-back .brand {
    position: absolute; top: 140px; left: 48px;
  }
  .card-back .brand-name .line-main { font-size: 40px; }
  .card-back .brand-name .line-sub { font-size: 17px; }
  .divider {
    position: absolute; left: 380px; top: 110px; width: 2px; height: 150px;
    background: var(--accent);
  }
  .contact {
    position: absolute; left: 410px; top: 108px;
  }
  .contact-name {
    color: var(--accent); font-size: 21px; font-weight: 600; letter-spacing: 0.02em;
  }
  .contact-title {
    font-size: 18px; line-height: 1.3; letter-spacing: 0.04em; margin: 4px 0 10px;
  }
  .contact-list { list-style: none; }
  .contact-list li {
    display: flex; align-items: center; gap: 10px;
    font-size: 18px; letter-spacing: 0.05em; line-height: 1.45;
  }
  .contact-list svg { width: 13px; height: 13px; flex-shrink: 0; }
  .tagline {
    position: absolute; left: 0; right: 0; bottom: 30px;
    text-align: center; font-size: 19px; letter-spacing: 0.14em;
  }
</style>
</head>
<body>
<main class="stage">
  <section class="card card-front">
    <div class="brand">
      <span class="brand-dot"></span>
      <div class="brand-name"><span class="line-main">MORAVEL</span><span class="line-sub">AESTHETIC DOCTOR</span></div>
    </div>
    <p class="services">
      Dermal injectables<span class="sep">|</span>Plasma facials<span class="sep">|</span>Microneedling<br>
      Skin boosters<span class="sep">|</span>Excessive sweating
    </p>
  </section>

  <section class="card card-back">
    <div class="brand">
      <span class="brand-dot"></span>
      <div class="brand-name"><span class="line-main">MORAVEL</span><span class="line-sub">AESTHETIC DOCTOR</span></div>
    </div>
    <span class="divider"></span>
    <div class="contact">
      <p class="contact-name">Dr Elise Varn MRCPCH MD</p>
      <p class="contact-title">Australasian Diploma<br>of Aesthetic Medicine</p>
      <ul class="contact-list">
        <li>
          <svg viewBox="0 0 16 16" aria-hidden="true"><path d="M4 1.5l2.5 3-1.5 1.5c.8 1.8 2.2 3.2 4 4l1.5-1.5 3 2.5-1.5 2.5C7 13.5 2.5 9 1.5 3z" fill="none" stroke="#12a9e8" stroke-width="1.4" stroke-linejoin="round"/></svg>
          0800 555 014
        </li>
        <li>
          <svg viewBox="0 0 16 16" aria-hidden="true"><rect x="1.5" y="3.5" width="13" height="9" fill="none" stroke="#12a9e8" stroke-width="1.4"/><path d="M1.5 3.5l6.5 5 6.5-5" fill="none" stroke="#12a9e8" stroke-width="1.4"/></svg>
          elise@moravel.co.nz
        </li>
        <li>
          <svg viewBox="0 0 16 16" aria-hidden="true"><circle cx="8" cy="8" r="6.5" fill="none" stroke="#12a9e8" stroke-width="1.3"/><ellipse cx="8" cy="8" rx="3" ry="6.5" fill="none" stroke="#12a9e8" stroke-width="1.1"/><path d="M1.5 8h13" stroke="#12a9e8" stroke-width="1.1"/></svg>
          www.moravel.co.nz
        </li>
      </ul>
    </div>
    <p class="tagline">HOME AND SPA BASED TREATMENTS</p>
  </section>
</main>
</body>
</html>
```